Design NEW business card

We would like a business card using the colour deep red wine or dark navy blue textured background (patterned or not, open to suggestions) with a high gloss debossed rose gold/copper RM Roland Mercer Jewellery business name (Provided). I have included images for your review we would like to keep our currently logo and business name on the front but you can change the layout and positioning. For the back of the card we are open to all suggestions/variations.
Business
Use our current RM Roland Mercer Jewellery logo (Provided image)

```html
<!DOCTYPE html>
<html lang="en">
<head>
<meta charset="UTF-8">
<title>Roland Mercer Jewellery – Business Card</title>
<link href="https://fonts.googleapis.com/css2?family=Montserrat:wght@400&family=Open+Sans:wght@400&display=swap" rel="stylesheet">
<style>
  :root {
    --backdrop: #cbaf96;
    --wine: #561c23;
    --copper: #a8764e;
    --copper-deep: #7a4a2e;
    --ink-muted: #3f1218;
  }
  * { margin: 0; padding: 0; box-sizing: border-box; }
  html, body {
    width: 1200px;
    height: 1200px;
    overflow: hidden;
    background: var(--backdrop);
  }
  .canvas {
    position: relative;
    width: 1200px;
    height: 1200px;
  }
  .card {
    position: absolute;
    left: 281px;
    width: 637px;
    height: 362px;
    background: var(--wine);
  }
  .card--front { top: 181px; }
  .card--back  { top: 634px; }

  .brand {
    position: absolute;
    left: 0;
    right: 0;
    display: flex;
    align-items: center;
    justify-content: center;
    gap: 22px;
    font-family: "Montserrat", sans-serif;
    font-weight: 400;
    color: var(--copper);
  }
  .card--front .brand { top: 200px; }
  .card--back .brand { top: 196px; }
  .brand__dot {
    width: 46px;
    height: 46px;
    border-radius: 50%;
    background: var(--copper);
    flex: none;
  }
  .brand__name {
    display: flex;
    flex-direction: column;
    align-items: flex-start;
    line-height: 1;
  }
  .brand__title {
    font-size: 27px;
    letter-spacing: 7px;
  }
  .brand__sub {
    margin-top: 12px;
    font-size: 9px;
    letter-spacing: 20px;
  }
  .card--back .brand { color: var(--copper-deep); }
  .card--back .brand__dot { background: var(--copper-deep); }

  .holder {
    position: absolute;
    left: 42px;
    bottom: 40px;
    font-family: "Open Sans", sans-serif;
    color: var(--ink-muted);
  }
  .holder__name { font-size: 15px; }
  .holder__role { font-size: 11px; margin-top: 2px; }

  .contact {
    position: absolute;
    right: 50px;
    bottom: 36px;
    list-style: none;
    text-align: right;
    font-family: "Open Sans", sans-serif;
    font-size: 11px;
    line-height: 22px;
    color: var(--ink-muted);
  }
</style>
</head>
<body>
<main class="canvas">
  <section class="card card--front" aria-label="Card front">
    <div class="brand">
      <span class="brand__dot" aria-hidden="true"></span>
      <div class="brand__name">
        <span class="brand__title">ROLAND MERCER</span>
        <span class="brand__sub">JEWELLERY</span>
      </div>
    </div>
  </section>

  <section class="card card--back" aria-label="Card back">
    <div class="brand">
      <span class="brand__dot" aria-hidden="true"></span>
      <div class="brand__name">
        <span class="brand__title">ROLAND MERCER</span>
        <span class="brand__sub">JEWELLERY</span>
      </div>
    </div>
    <div class="holder">
      <p class="holder__name">Your Full Name</p>
      <p class="holder__role">Designation</p>
    </div>
    <ul class="contact">
      <li>(03)+ 98-765-432</li>
      <li>info@rmjewellery.com</li>
      <li>www.rmjewellery.com</li>
    </ul>
  </section>
</main>
</body>
</html>
```